Clear Path Keystone Realty yard sign Logo

UPDATE Design logo for Realty yard sign. 24x24 diamond or 36x24 Rectangle.
Open to all ideas. We are a discount firm but want to project a high end feel. We provide 100% of all services and extensive marketing for 1/2 the fee.
The following info must be on sign
CLEAR PATH KEYSTONE (OR K) REALTY
Doran Pike 547-6093
KeystonePX.com

Target Market(s)

home sellers and buyers

Industry/Entity Type

Real Estate yard sign please see sign attached in gif

Logo Text

Clear Path Keystone Realty OR (K IN PLACE OF KEYSTONE)

Requirements
Must have
• CLEAR PATH KEYSTONE (OR K) REALTY Doran Pike 547-6093 KeystonePX.com FOR SALE (optional)

```html
<!DOCTYPE html>
<html lang="en">
<head>
<meta charset="utf-8">
<title>Clear Path Keystone Realty — Yard Sign</title>
<link rel="stylesheet" href="https://fonts.googleapis.com/css2?family=Fraunces:opsz,wght@144,900&family=Arimo:wght@700&display=swap">
<style>
  :root {
    --navy: #0b1450;
    --gold: #e8c20c;
    --white: #ffffff;
    --page: #f2f1ec;
  }
  html, body {
    margin: 0;
    padding: 0;
    width: 1200px;
    height: 1199px;
    overflow: hidden;
    background: var(--page);
  }
  .yard-sign {
    position: relative;
    width: 1200px;
    height: 1199px;
  }
  .sign-panel {
    position: absolute;
    inset: 0;
  }
  .sign-copy {
    position: absolute;
    left: 0;
    width: 1200px;
    text-align: center;
    color: var(--white);
    margin: 0;
  }
  .brand-dot {
    position: absolute;
    left: 555px;
    top: 205px;
    width: 90px;
    height: 90px;
    border-radius: 50%;
    background: var(--gold);
  }
  .headline {
    top: 360px;
    font-family: "Fraunces", Georgia, serif;
    font-weight: 900;
    font-size: 64px;
    line-height: 1;
    letter-spacing: 1px;
  }
  .brand-name {
    font-family: "Fraunces", Georgia, serif;
    font-weight: 900;
    line-height: 1;
  }
  .brand-name-primary {
    top: 460px;
    font-size: 118px;
  }
  .brand-name-secondary {
    top: 600px;
    font-size: 60px;
    letter-spacing: 2px;
  }
  .agent-line,
  .web-line {
    font-family: "Arimo", Arial, sans-serif;
    font-weight: 700;
    font-size: 38px;
    line-height: 1;
  }
  .agent-line { top: 712px; }
  .web-line { top: 762px; }
</style>
</head>
<body>
  <main class="yard-sign">
    <svg class="sign-panel" width="1200" height="1199" viewBox="0 0 1200 1199" aria-hidden="true">
      <polygon points="600,48 1152,600 600,1152 48,600" fill="var(--gold)"/>
      <polygon points="600,68 1132,600 600,1132 68,600" fill="var(--navy)"/>
    </svg>

    <span class="brand-dot" aria-hidden="true"></span>
    <p class="sign-copy headline">FOR SALE</p>
    <p class="sign-copy brand-name brand-name-primary">Clear Path</p>
    <p class="sign-copy brand-name brand-name-secondary">KEYSTONE REALTY</p>
    <p class="sign-copy agent-line">Doran Pike 547-6093</p>
    <p class="sign-copy web-line">KeystonePX.com</p>
  </main>
</body>
</html>
```